Harrowgate Care Assurance Ltd needs a business card and logo

We need a logo for documents, invoices etc and a business card to match. We are a health auditing, training and consulting company based in NZ and working in both Australia and NZ. We ensure health organisations meet all their compliance requirements and develop expertise in the health auditing sector. The design should in some way reflect either symbols for quality management in the health sector.

Target Market(s)

Health providers and those wishing to increase their capability in meeting and understanding compliance requirements

Industry/Entity Type

Business

Contact Information for Business Card

Logo plus contact details

Logo Text

Health auditing, consultancy and training

Requirements
Must have
• Name and contact details director: Marla Fenwick, mfenwick@hca-example.co.nz, PO Box 318, Tarrowdale, NZ, cell +6427391652

```html
<!DOCTYPE html>
<html lang="en">
<head>
<meta charset="utf-8">
<title>Harrowgate Care Assurance Ltd – Business Card and Logo</title>
<link rel="stylesheet" href="https://fonts.googleapis.com/css2?family=Montserrat:wght@400;500;600&display=swap">
<style>
  :root {
    --bg: #e4dadb;
    --brand-blue: #1272b8;
    --card-blue: #0a95d0;
    --card-blue-deep: #0579ba;
    --accent-red: #e8262b;
    --ink: #2a2a2a;
    --paper: #ffffff;
  }
  * { margin: 0; padding: 0; box-sizing: border-box; }
  html, body { width: 1200px; height: 1129px; overflow: hidden; }
  body {
    background: var(--bg);
    font-family: "Montserrat", sans-serif;
    position: relative;
  }
  .card {
    position: absolute;
    width: 540px;
    height: 310px;
    border-radius: 4px;
    box-shadow: 0 10px 24px rgba(0,0,0,0.12);
  }
  .card--back {
    left: 620px;
    top: 150px;
    background: linear-gradient(135deg, var(--card-blue), var(--card-blue-deep));
    display: flex;
    align-items: center;
    justify-content: center;
  }
  .card--front {
    left: 40px;
    top: 150px;
    background: var(--paper);
    display: flex;
    align-items: center;
    padding: 0 34px;
  }
  .brand {
    display: flex;
    align-items: center;
    gap: 12px;
  }
  .brand__mark {
    flex: none;
    border-radius: 50%;
  }
  .brand__name {
    font-weight: 600;
    line-height: 1.15;
  }
  .card--back .brand__mark { width: 42px; height: 42px; background: var(--paper); }
  .card--back .brand__name { color: var(--paper); font-size: 26px; }
  .card--front .brand { width: 210px; }
  .card--front .brand__mark { width: 28px; height: 28px; background: var(--brand-blue); }
  .card--front .brand__name { color: var(--brand-blue); font-size: 17px; }
  .divider {
    width: 2px;
    height: 160px;
    background: var(--brand-blue);
    margin: 0 26px;
    flex: none;
  }
  .contact__name {
    font-size: 24px;
    font-weight: 500;
    color: var(--ink);
  }
  .contact__role {
    font-size: 15px;
    color: var(--brand-blue);
    margin-bottom: 18px;
  }
  .contact__list { list-style: none; }
  .contact__item {
    display: flex;
    align-items: center;
    gap: 8px;
    font-size: 12.5px;
    font-weight: 500;
    color: var(--ink);
    margin-bottom: 7px;
    white-space: nowrap;
  }
  .contact__icon { width: 13px; height: 13px; flex: none; }
  .logo {
    position: absolute;
    left: 50px;
    top: 900px;
    display: flex;
    align-items: center;
    gap: 22px;
  }
  .logo__mark {
    width: 78px;
    height: 78px;
    border-radius: 50%;
    background: var(--brand-blue);
  }
  .logo__name {
    font-size: 52px;
    font-weight: 600;
    color: var(--brand-blue);
  }
</style>
</head>
<body>

  <section class="card card--front">
    <div class="brand">
      <span class="brand__mark"></span>
      <span class="brand__name">Harrowgate Care Assurance Ltd</span>
    </div>
    <div class="divider"></div>
    <div class="contact">
      <p class="contact__name">Marla Fenwick</p>
      <p class="contact__role">Director</p>
      <ul class="contact__list">
        <li class="contact__item">
          <svg class="contact__icon" viewBox="0 0 16 16" aria-hidden="true"><rect x="1" y="3" width="14" height="10" fill="#e8262b"/><path d="M1 3l7 6 7-6" fill="none" stroke="#fff" stroke-width="1.4"/></svg>
          mfenwick@hca-example.co.nz
        </li>
        <li class="contact__item">
          <svg class="contact__icon" viewBox="0 0 16 16" aria-hidden="true"><rect x="3" y="1" width="10" height="14" rx="2" fill="none" stroke="#e8262b" stroke-width="1.6"/><circle cx="8" cy="12" r="1" fill="#e8262b"/></svg>
          +6427391652
        </li>
        <li class="contact__item">
          <svg class="contact__icon" viewBox="0 0 16 16" aria-hidden="true"><path d="M8 15s5-5.5 5-9A5 5 0 0 0 3 6c0 3.5 5 9 5 9z" fill="#e8262b"/><circle cx="8" cy="6" r="1.8" fill="#fff"/></svg>
          PO Box 318, Tarrowdale, NZ,
        </li>
      </ul>
    </div>
  </section>

  <section class="card card--back">
    <div class="brand">
      <span class="brand__mark"></span>
      <span class="brand__name">Harrowgate Care<br>Assurance Ltd</span>
    </div>
  </section>

  <div class="logo">
    <span class="logo__mark"></span>
    <span class="logo__name">Harrowgate Care Assurance Ltd</span>
  </div>

</body>
</html>
```